Maranoola Wines - web page for new Australian wine label

We need a landing page for our wine company. Maranoola is a family owned company, we grow the gapes, and make the wine in the Clare valley. Daniel Whitlock is the winemaker and is well known for his style, which is all about the fruit flavour rather than wood or age influences. Maranoola is Abriginal for 2 hills and a water source. We hand pick, hand plunge, foot crush resulting in elegant wine. Little to no additives, minimal filtering, single vineyard wines. Handcrafted with small releases of only the best fruit from carefully selected rows and bunches. The Clare valley is located two hours North of Adelaide, is known for cool climate and slow ripening, resulting in wines that have an elegant mouth feel, with bright colour and outstanding flavours. Our Brookmere vineyard has a Eastern aspect, gathering morning sun and escaping the hot afternoons, and in our opinion is on of the prettiest valleys in the world. Only 1000 cases per annum of the very best handpicked fruit, from the best rows. We hope you enjoy the Maranoola style, the reds are lighter in colour, fruit driven palate, more old world influence and the Riesling is on the dry side with fresh citrus. Minimal additives and filtering, our aim was to make wine with minimal influence from wine making. Handcrafted wines.

Target Market(s)

females 18 - 60 are the ones that buy 70 percent of wine, so whilst men are also a target, its the ladies we seek to appeal to.

Industry/Entity Type

It Company

Number of Pages Required

4 page

Font styles to use
Serif

Requirements
Must have
• Eye catching front page that makes me feel like i am ordering from quality company, that cares for what they do. Easy to use ordering, and delivery instructions.
• postage is $14.90 per case Australia wide.
• www.maranoolawines-example.com
Nice to have
• I want to see a fun and family oriented business that cares for the wine, we dont make a lot, its buckets and feet. But its wine made wanting to be the best in the world, we dont cut corners on quality. Handcrafted
Should not have
• dont really have any thoughts here, looking for all ideas

```html
<!DOCTYPE html>
<html lang="en">
<head>
<meta charset="utf-8">
<title>Maranoola Wines</title>
<link rel="stylesheet" href="https://fonts.googleapis.com/css2?family=Great+Vibes&family=Nunito+Sans:wght@400;600;700&family=Open+Sans:wght@400;600&display=swap">
<style>
:root{
  --blue:#0b57b4;
  --blue-dark:#0a3f86;
  --navy:#0c1a2c;
  --ink:#2b2b2b;
  --muted:#6b6b6b;
  --line:#cfcfcf;
  --white:#ffffff;
}
*{box-sizing:border-box;margin:0;padding:0}
html,body{width:1200px;height:2941px;overflow:hidden}
body{position:relative;background:var(--white);font-family:"Open Sans",Arial,sans-serif;color:var(--ink)}
section,header,footer{position:absolute;left:0;width:1200px}
.photo{position:absolute}

/* header */
.site-header{top:0;height:94px;background:var(--white);box-shadow:0 1px 4px rgba(0,0,0,.08);z-index:2}
.brand{position:absolute;left:154px;top:24px;font-family:"Nunito Sans",sans-serif;font-weight:700;font-size:34px;color:var(--blue);letter-spacing:.5px}
.main-nav{position:absolute;right:155px;top:40px;display:flex;gap:28px;font-family:"Nunito Sans",sans-serif;font-size:15px;color:#333;text-transform:uppercase}
.main-nav .active{color:var(--blue)}

/* hero */
.hero{top:94px;height:541px;overflow:hidden}
.hero .photo{inset:0;background:
  radial-gradient(ellipse 30% 40% at 12% 20%,rgba(48,38,66,.85),transparent 70%),
  radial-gradient(ellipse 28% 38% at 88% 75%,rgba(40,34,62,.85),transparent 70%),
  radial-gradient(ellipse 25% 30% at 70% 15%,rgba(90,120,60,.9),transparent 70%),
  radial-gradient(ellipse 35% 35% at 30% 80%,rgba(110,100,70,.8),transparent 70%),
  linear-gradient(160deg,#4a6432 0%,#3a5226 50%,#2a3a1c 100%)}
.hero .shade{position:absolute;inset:0;background:rgba(0,0,0,.12)}
.hero-title{position:absolute;top:176px;width:100%;text-align:center;font-family:"Nunito Sans",sans-serif;font-weight:600;font-size:48px;color:var(--white);text-shadow:0 2px 6px rgba(0,0,0,.4)}
.hero-script{position:absolute;top:232px;width:100%;text-align:center;font-family:"Great Vibes",cursive;font-size:50px;color:var(--white);text-shadow:0 2px 6px rgba(0,0,0,.4)}
.btn{display:inline-block;background:var(--blue);color:var(--white);font-family:"Nunito Sans",sans-serif;font-weight:600;text-transform:uppercase;border-radius:24px;text-align:center}
.hero .btn{position:absolute;left:516px;top:320px;width:176px;height:46px;line-height:46px;font-size:15px;letter-spacing:.5px}
.slider-dots{position:absolute;top:508px;left:546px;display:flex;gap:6px}
.slider-dots i{display:block;width:24px;height:3px;background:rgba(255,255,255,.8)}
.slider-dots i.on{background:var(--blue)}

/* welcome */
.welcome{top:635px;height:545px}
.script-title{position:absolute;top:42px;width:100%;text-align:center;font-family:"Great Vibes",cursive;font-size:54px;color:var(--blue)}
.divider{position:absolute;top:112px;left:524px;width:152px;height:1px;background:var(--line)}
.divider::after{content:"";position:absolute;left:68px;top:0;border:8px solid transparent;border-top-color:#bfbfbf}
.family-photo{left:440px;top:154px;width:320px;height:320px;border-radius:50%;background:
  radial-gradient(circle at 30% 30%,rgba(200,170,90,.75),transparent 45%),
  radial-gradient(circle at 75% 70%,rgba(190,150,70,.6),transparent 40%),
  linear-gradient(180deg,#6d5a3e 0%,#3a3040 60%,#2a2632 100%);border:4px solid var(--white);box-shadow:0 0 0 3px #1c1c1c}
.feature{position:absolute;width:290px}
.feature h3{font-family:"Nunito Sans",sans-serif;font-weight:600;font-size:17px;color:var(--blue);margin-bottom:6px}
.feature p{font-size:10.5px;line-height:17px;color:var(--muted)}
.feature.left{text-align:right}
.feature-icon{position:absolute;width:88px;height:88px;border-radius:50%;border:2px solid var(--blue);display:flex;align-items:center;justify-content:center}
.feature-icon::before{content:"";position:absolute;inset:5px;border-radius:50%;border:1px solid var(--blue)}

/* band */
.craft-band{top:1180px;height:425px;overflow:hidden}
.craft-band .photo{inset:0;background:
  radial-gradient(ellipse 22% 40% at 92% 40%,rgba(150,70,50,.85),transparent 70%),
  radial-gradient(ellipse 30% 30% at 60% 85%,rgba(160,60,60,.75),transparent 70%),
  radial-gradient(ellipse 25% 35% at 55% 35%,rgba(170,150,140,.6),transparent 70%),
  linear-gradient(120deg,#3a3634 0%,#4e4440 45%,#2c2826 100%)}
.craft-band .shade{position:absolute;inset:0;background:rgba(0,0,0,.3)}
.craft-box{position:absolute;left:245px;top:102px;width:688px;height:212px;border:2px solid rgba(255,255,255,.85);text-align:center;color:var(--white);font-family:"Nunito Sans",sans-serif}
.craft-box h2{font-weight:400;font-size:36px;margin-top:24px}
.craft-box .sub{font-size:24px;margin-top:2px}
.craft-box p{font-family:"Open Sans",sans-serif;font-size:17px;line-height:24px;margin-top:8px}

/* wine */
.our-wine{top:1605px;height:415px}
.our-wine .photo{left:0;top:0;width:603px;height:415px;background:
  radial-gradient(ellipse 20% 45% at 60% 65%,rgba(40,36,40,.9),transparent 70%),
  radial-gradient(ellipse 28% 22% at 22% 78%,rgba(200,60,40,.75),transparent 70%),
  linear-gradient(180deg,#5f9fd8 0%,#a9cbe8 20%,#6fb3c4 26%,#e8e2d6 34%,#ede8de 70%,#d6d2cc 100%)}
.wine-panel{position:absolute;left:603px;top:0;width:597px;height:415px;background:var(--blue);color:var(--white);text-align:center}
.wine-panel h2{font-family:"Nunito Sans",sans-serif;font-weight:400;font-size:34px;margin-top:68px}
.wine-panel p{font-size:13.5px;line-height:23px;width:380px;margin:14px auto 0}
.wine-panel p+p{margin-top:16px}
.wine-panel .btn{margin-top:22px;width:148px;height:38px;line-height:38px;font-size:13px;background:var(--blue-dark)}

/* how we make */
.how-we-make{top:2020px;height:470px}
.section-title{position:absolute;top:36px;width:100%;text-align:center;font-family:"Nunito Sans",sans-serif;font-weight:400;font-size:31px;color:var(--ink)}
.make-grid{position:absolute;left:169px;top:87px;width:874px;height:328px;border:1px solid var(--line);display:grid;grid-template-columns:repeat(3,1fr);grid-template-rows:repeat(2,1fr)}
.make-grid .tile{position:relative;background:var(--white);text-align:center}
.make-grid .tile.img{background:radial-gradient(ellipse 30% 45% at 40% 60%,rgba(190,90,60,.7),transparent 70%),linear-gradient(135deg,#6f7d52,#3d4630)}
.make-grid .tile.img.steel{background:radial-gradient(ellipse 35% 45% at 70% 60%,rgba(200,200,205,.7),transparent 70%),linear-gradient(135deg,#5a6a4e,#3a3f45)}
.make-grid .tile.img.shed{background:radial-gradient(ellipse 40% 30% at 55% 85%,rgba(230,200,40,.8),transparent 70%),linear-gradient(135deg,#8a7a56,#3c3a34)}
.tile h3{font-family:"Nunito Sans",sans-serif;font-weight:600;font-size:20px;color:var(--blue);margin-top:16px}
.tile p{font-size:11.5px;line-height:19px;color:#555;width:250px;margin:8px auto 0}
.tile .more{display:block;font-size:11.5px;color:#222;margin-top:9px;text-transform:uppercase}

/* delivery */
.delivery{top:2490px;height:272px;overflow:hidden}
.delivery .photo{inset:0;background:
  radial-gradient(ellipse 18% 50% at 10% 60%,rgba(60,150,120,.55),transparent 70%),
  radial-gradient(ellipse 18% 50% at 88% 55%,rgba(60,150,120,.5),transparent 70%),
  linear-gradient(90deg,#0b4fa8 0%,#1a66c4 50%,#0b4fa8 100%)}
.notch{position:absolute;left:580px;top:0;border:20px solid transparent;border-top-color:var(--white)}
.delivery-text{position:absolute;top:44px;width:100%;text-align:center;color:var(--white)}
.delivery-text h2{font-family:"Nunito Sans",sans-serif;font-weight:400;font-size:25px;line-height:30px;margin-top:14px}
.delivery-text p{font-size:13.5px;line-height:23px;width:600px;margin:8px auto 0;opacity:.9}

/* footer */
.site-footer{top:2762px;height:179px;background:var(--navy);color:var(--white);text-align:center}
.foot-nav{display:flex;justify-content:center;gap:26px;font-family:"Nunito Sans",sans-serif;font-size:14px;text-transform:uppercase;margin-top:36px}
.copyright{font-size:11.5px;color:#b7bec8;margin-top:12px}
.social{display:flex;justify-content:center;gap:6px;margin-top:20px}
.social span{display:block;width:28px;height:28px;border-radius:50%;border:1.5px solid var(--white)}
</style>
</head>
<body>

<header class="site-header">
  <div class="brand">Maranoola</div>
  <nav class="main-nav">
    <span class="active">Home</span><span>About Us</span><span>Wine</span><span>How We Make</span><span>Shop Now</span><span>Review</span><span>Contact</span>
  </nav>
</header>

<section class="hero">
  <div class="photo" role="img" aria-label="Vineyard rows with bunches of dark red grapes among green leaves"></div>
  <div class="shade"></div>
  <h1 class="hero-title">We Make Elegant Wine</h1>
  <div class="hero-script">Try, You love it</div>
  <a class="btn">Shop Now</a>
  <div class="slider-dots"><i></i><i></i><i class="on"></i><i></i></div>
</section>

<section class="welcome">
  <h2 class="script-title">Welcome to Maranoola</h2>
  <div class="divider"></div>
  <div class="photo family-photo" role="img" aria-label="The winemaking family gathered in the barrel room"></div>

  <div class="feature left" style="left:48px;top:180px"><h3>100% Natural</h3><p>Morbi diam mauris viverra in gravida eu<br>mattis in ante Morbi eget arcu Morbi<br>porta libero id ullamcorper</p></div>
  <div class="feature-icon" style="left:352px;top:176px"><svg width="40" height="40" viewBox="0 0 40 40" fill="none" stroke="#0b57b4" stroke-width="2"><circle cx="14" cy="16" r="4"/><circle cx="22" cy="16" r="4"/><circle cx="30" cy="16" r="4"/><circle cx="18" cy="23" r="4"/><circle cx="26" cy="23" r="4"/><circle cx="22" cy="30" r="4"/><path d="M22 12 L24 5"/></svg></div>

  <div class="feature" style="left:857px;top:180px"><h3>Owning Family</h3><p>Morbi diam mauris viverra in gravida eu<br>mattis in ante Morbi eget arcu Morbi<br>porta libero id ullamcorper</p></div>
  <div class="feature-icon" style="left:758px;top:176px"><svg width="40" height="40" viewBox="0 0 40 40" fill="#0b57b4"><circle cx="14" cy="12" r="5"/><circle cx="26" cy="12" r="5"/><path d="M5 32 C5 22 23 22 23 32Z"/><path d="M17 32 C17 22 35 22 35 32Z"/></svg></div>

  <div class="feature left" style="left:48px;top:375px"><h3>Top Quality</h3><p>Morbi diam mauris viverra in gravida eu<br>mattis in ante Morbi eget arcu Morbi<br>porta libero id ullamcorper</p></div>
  <div class="feature-icon" style="left:352px;top:371px"><svg width="40" height="40" viewBox="0 0 40 40" fill="none" stroke="#0b57b4" stroke-width="2"><circle cx="20" cy="15" r="10"/><circle cx="20" cy="15" r="5"/><path d="M14 23 L11 36 L16 33 L18 37 L20 25"/><path d="M26 23 L29 36 L24 33 L22 37 L20 25"/></svg></div>

  <div class="feature" style="left:870px;top:375px"><h3>Always Fresh</h3><p>Morbi diam mauris viverra in gravida eu<br>mattis in ante Morbi eget arcu Morbi<br>porta libero id ullamcorper</p></div>
  <div class="feature-icon" style="left:770px;top:371px"><svg width="40" height="40" viewBox="0 0 40 40" fill="none" stroke="#0b57b4" stroke-width="2"><path d="M17 4 H23 V12 C28 15 28 18 28 22 V36 H12 V22 C12 18 12 15 17 12Z"/><rect x="15" y="22" width="10" height="8"/></svg></div>
</section>

<section class="craft-band">
  <div class="photo" role="img" aria-label="Children foot crushing grapes in large tubs in the winery"></div>
  <div class="shade"></div>
  <div class="craft-box">
    <h2>We hand pick, hand plunge, foot</h2>
    <div class="sub">crush resulting in elegant wine</div>
    <p>Only 1000 cases per annum of the very best handpicked<br>fruit, from the best rows</p>
  </div>
</section>

<section class="our-wine">
  <div class="photo" role="img" aria-label="A bottle of white wine beside a bowl of crayfish on a sunny beach"></div>
  <div class="wine-panel">
    <h2>Our Wine</h2>
    <p>elerisque mi tortor at ipsum cligula augue bibendum accumsan vestibulum ut commodo a</p>
    <p>Ami Morbi ornare gravida elit Integer congue augue et malesuada iaculis ipsum dui aliquet felis at cursus magna nisl nec elit Praesent elementum elit at tellus</p>
    <a class="btn">Buy Now</a>
  </div>
</section>

<section class="how-we-make">
  <h2 class="section-title">How We Make</h2>
  <div class="make-grid">
    <div class="tile img" role="img" aria-label="Picking grape bunches by hand in the vineyard"></div>
    <div class="tile"><h3>Tittle here</h3><p>Class aptent taciti sociosqu ad litora torquent per conubia nostra per inceptos hymenaeos Proin nulla arcu nonummy luctus</p><span class="more">Read More</span></div>
    <div class="tile img steel" role="img" aria-label="Working at the stainless steel wine press"></div>
    <div class="tile"><h3>Tittle here</h3><p>Class aptent taciti sociosqu ad litora torquent per conubia nostra per inceptos hymenaeos Proin nulla arcu nonummy luctus</p><span class="more">Read More</span></div>
    <div class="tile img shed" role="img" aria-label="Winemaker on a forklift in the winery shed"></div>
    <div class="tile"><h3>Tittle here</h3><p>Class aptent taciti sociosqu ad litora torquent per conubia nostra per inceptos hymenaeos Proin nulla arcu nonummy luctus</p><span class="more">Read More</span></div>
  </div>
</section>

<section class="delivery">
  <div class="photo" role="img" aria-label="Friends enjoying wine outdoors, tinted blue"></div>
  <div class="notch"></div>
  <div class="delivery-text">
    <svg width="80" height="50" viewBox="0 0 80 50" fill="none" stroke="#fff" stroke-width="2.5"><rect x="6" y="6" width="42" height="30"/><path d="M48 16 H62 L72 27 V36 H48Z"/><circle cx="20" cy="40" r="5" fill="#1a66c4"/><circle cx="60" cy="40" r="5" fill="#1a66c4"/><path d="M0 14 H10 M0 22 H10 M0 30 H10"/></svg>
    <h2>Delivery charge is $14.90 per case<br>Australia wide</h2>
    <p>Praesent elementum elit at tellus nec ultricies sit amet porttitor mattis enim In massa libero interdum nec interdum nec blandit sed nulla In</p>
  </div>
</section>

<footer class="site-footer">
  <nav class="foot-nav"><span>Home</span><span>About Us</span><span>Wine</span><span>How We Make</span><span>Shop Now</span><span>Review</span><span>Contact</span></nav>
  <div class="copyright">© 2017 Company Name &nbsp;All right reserved &nbsp;Term of Use</div>
  <div class="social"><span></span><span></span><span></span><span></span></div>
</footer>

</body>
</html>
```